VENTURE CAPITAL GROUP BUSINESS CARD DESIGN

Venture Capital Group based in SF looking for a bold business card design. No trendy colour explosion, 3D effects etc. Just "simple" optical effects. Works on your brain, keeps your eye focused and sticks to your mind.
Target Market(s)
Technology startups
Industry/Entity Type
Venture Capital
Contact Information for Business Card
DESMOND WHITLAKE
MANAGING PARTNER
187 FENWORTH ST SAN FRANCISCO, CA 94187
415.555.0142 O
415.555.0147 F
415.555.0193 C
desmond@veldtmoorcapital.ventures

```html
<!DOCTYPE html>
<html lang="en">
<head>
<meta charset="utf-8">
<title>Veldtmoor Capital Group – Business Card</title>
<link href="https://fonts.googleapis.com/css2?family=PT+Sans:wght@400;700&display=swap" rel="stylesheet">
<style>
  :root {
    --stage: #000000;
    --card-front: #f3f3f3;
    --green-brand: #1f7a2d;
    --green-top: #56b54f;
    --green-mid: #2a8a36;
    --green-bottom: #0b4416;
    --ink: #1c1c1c;
    --white: #ffffff;
    --disc-light: #ffffff;
    --disc-shade: #dcdcdc;
  }
  * { box-sizing: border-box; margin: 0; padding: 0; }
  html, body {
    width: 1200px; height: 900px; overflow: hidden;
    background: var(--stage);
    font-family: "PT Sans", "Myriad Pro", Arial, sans-serif;
  }
  .stage { position: relative; width: 1200px; height: 900px; }

  .card { position: absolute; top: 200px; width: 310px; height: 502px; overflow: hidden; }

  .card--front {
    left: 265px;
    background: var(--card-front);
    border-radius: 46px 0 46px 0;
  }
  .brand-disc {
    position: absolute; left: 386px; left: 121px; top: 38px;
    width: 102px; height: 102px; border-radius: 50%;
    background: radial-gradient(circle at 40% 35%, var(--disc-light) 0%, var(--disc-shade) 100%);
  }
  .brand-name {
    position: absolute; left: 0; right: 0; top: 156px;
    text-align: center; color: var(--green-brand);
    font-weight: 400; line-height: 1;
  }
  .brand-name .word { display: block; font-size: 31px; letter-spacing: 2px; padding-left: 60px; }
  .brand-name .sub { display: block; font-size: 8px; letter-spacing: 3px; margin-top: 3px; padding-left: 60px; }

  .contact { position: absolute; left: 32px; top: 289px; color: var(--ink); }
  .contact__name { font-size: 17px; font-weight: 700; color: var(--green-brand); line-height: 1.2; }
  .contact__role { font-size: 13px; line-height: 1.3; margin-top: 1px; }
  .contact__address { font-size: 13px; line-height: 18px; margin-top: 17px; }
  .contact__lines { list-style: none; margin-top: 14px; font-size: 13px; }
  .contact__lines li { display: flex; align-items: center; height: 20.5px; }
  .contact__lines svg { width: 10px; height: 10px; margin-right: 4px; fill: var(--green-brand); flex: none; }

  .card--back {
    left: 641px;
    border-radius: 0 46px 0 46px;
    background: linear-gradient(180deg, var(--green-top) 0%, var(--green-mid) 42%, var(--green-bottom) 100%);
  }
  .back-glow {
    position: absolute; inset: 0;
    background: radial-gradient(ellipse 70% 45% at 55% 45%, rgba(255,255,255,0.08), rgba(255,255,255,0) 70%);
  }
  .back-brand {
    position: absolute; left: 0; right: 0; top: 414px;
    text-align: center; color: var(--white); font-weight: 400; line-height: 1;
  }
  .back-brand .word { display: block; font-size: 31px; letter-spacing: 2px; }
  .back-brand .sub { display: block; font-size: 8px; letter-spacing: 3px; margin-top: 3px; }
</style>
</head>
<body>
<main class="stage">
  <section class="card card--front" aria-label="Business card front">
    <div class="brand-disc"></div>
    <div class="brand-name">
      <span class="word">VELDTMOOR</span>
      <span class="sub">CAPITAL GROUP</span>
    </div>
    <div class="contact">
      <p class="contact__name">Desmond Whitlake</p>
      <p class="contact__role">Managing Partner</p>
      <p class="contact__address">187 Fenworth St San<br>Francisco, CA 94187</p>
      <ul class="contact__lines">
        <li><svg viewBox="0 0 10 10" aria-hidden="true"><path d="M2 0.5 L3.6 2.6 L2.7 3.7 Q3.6 5.8 6.3 7.3 L7.4 6.4 L9.5 8 L8.3 9.5 Q4.5 9.4 1.6 5.7 Q0.3 3.6 0.6 1.6 Z"/></svg>415.555.0142</li>
        <li><svg viewBox="0 0 10 10" aria-hidden="true"><path d="M1 3 H9 V9 H1 Z M2.5 0.5 H7.5 V2.5 H2.5 Z"/></svg>415.555.0147</li>
        <li><svg viewBox="0 0 10 10" aria-hidden="true"><path d="M2.5 0 H7.5 V10 H2.5 Z M3.5 1.2 V7.8 H6.5 V1.2 Z" fill-rule="evenodd"/></svg>415.555.0193</li>
        <li><svg viewBox="0 0 10 10" aria-hidden="true"><path d="M0.5 2 H9.5 V8.5 H0.5 Z M0.9 2.3 L5 5.5 L9.1 2.3" /></svg>desmond@veldtmoorcapital.ventures</li>
      </ul>
    </div>
  </section>

  <section class="card card--back" aria-label="Business card back">
    <div class="back-glow"></div>
    <div class="back-brand">
      <span class="word">VELDTMOOR</span>
      <span class="sub">CAPITAL GROUP</span>
    </div>
  </section>
</main>
</body>
</html>
```